Request for Business Card Design

Hi. My name is Marlene, I am looking for a new business card design for my company, Quarrow Signal Instruments, LLC. I really like the design you did for Tarsel Venture and was hoping you could do something similar using our full logo and our mark. I am also open to any raised texture design using our mark. I have attached our full logo, which would need to be somewhere on the card, as well as the mark in both outline and full form, as well as our brand colors / guide. The card does not have to be white, as long as our logo and mark appear. I actually like darker colored business cards more, but am open to all options. If you are interested in working with me, please let me know. We would also take the business card design into letterhead design if you can do that.

```html
<!DOCTYPE html>
<html lang="en">
<head>
<meta charset="utf-8">
<title>Quarrow Signal Instruments — Business Card</title>
<link rel="stylesheet" href="https://fonts.googleapis.com/css2?family=Open+Sans:wght@400;600;700;800&display=swap">
<style>
  :root {
    --backdrop: #232323;
    --card: #1f1f22;
    --card-edge: #1a9bc7;
    --brand-blue: #1a9bc7;
    --brand-grey: #3c3c40;
    --text-light: #f2f2f2;
    --mark-shade: #141416;
  }
  * { box-sizing: border-box; margin: 0; padding: 0; }
  html, body {
    width: 1200px; height: 780px; overflow: hidden;
    background: var(--backdrop);
    font-family: "Open Sans", Arial, sans-serif;
  }
  .canvas { position: relative; width: 1200px; height: 780px; }

  .card {
    position: absolute;
    width: 560px; height: 320px;
    background: var(--card);
    border-left: 4px solid var(--card-edge);
    border-bottom: 4px solid var(--card-edge);
    box-shadow: 0 18px 30px rgba(0,0,0,.55);
    overflow: hidden;
  }
  .card--front { left: 70px; top: 70px; }
  .card--back  { left: 570px; top: 420px; }

  /* brand signature: one circle + name in one colour/weight */
  .brand { display: flex; align-items: center; gap: 14px; }
  .brand__dot { border-radius: 50%; background: var(--brand-blue); flex: none; }
  .brand__name {
    color: var(--brand-grey); font-weight: 800; text-transform: uppercase;
    line-height: 1.05; letter-spacing: .04em;
  }

  .card--front .brand { position: absolute; left: 100px; top: 115px; }
  .card--front .brand__dot { width: 70px; height: 70px; }
  .card--front .brand__name { font-size: 30px; }

  .card--back .brand { position: absolute; left: 34px; top: 38px; gap: 10px; }
  .card--back .brand__dot { width: 44px; height: 44px; }
  .card--back .brand__name { font-size: 19px; }

  .holder { position: absolute; right: 0; top: 30px; display: flex; align-items: flex-start; }
  .holder__text { text-align: right; margin-right: 10px; }
  .holder__name { color: var(--brand-blue); font-weight: 800; font-size: 32px; line-height: 1; }
  .holder__role { color: var(--text-light); font-weight: 600; font-size: 13px; margin-top: 2px; }
  .holder__bar { width: 22px; height: 46px; background: var(--brand-blue); }

  .mark-area {
    position: absolute; right: -40px; top: 110px;
    width: 250px; height: 250px; border-radius: 50%;
    background: radial-gradient(circle at 40% 30%, #2b2b2e, var(--mark-shade) 70%);
  }

  .contact { position: absolute; left: 34px; bottom: 26px; color: var(--text-light); }
  .contact__address { font-size: 13px; line-height: 1.35; margin-bottom: 12px; }
  .contact__list { list-style: none; font-size: 12.5px; line-height: 1.55; }
  .contact__list li { display: flex; align-items: center; gap: 8px; }
  .contact__list svg { width: 13px; height: 13px; fill: none; stroke: var(--brand-blue); stroke-width: 2; flex: none; }
</style>
</head>
<body>
<main class="canvas">

  <section class="card card--front" aria-label="Card front">
    <div class="brand">
      <span class="brand__dot"></span>
      <span class="brand__name">Quarrow Signal<br>Instruments</span>
    </div>
  </section>

  <section class="card card--back" aria-label="Card back">
    <div class="brand">
      <span class="brand__dot"></span>
      <span class="brand__name">Quarrow Signal<br>Instruments</span>
    </div>

    <div class="holder">
      <div class="holder__text">
        <p class="holder__name">Marlene</p>
        <p class="holder__role">Director</p>
      </div>
      <span class="holder__bar"></span>
    </div>

    <div class="mark-area" role="img" aria-label="Large raised brand mark area"></div>

    <div class="contact">
      <p class="contact__address">1180 Harlow Works Road &bull;<br>Ridgefield, CO 80611</p>
      <ul class="contact__list">
        <li><svg viewBox="0 0 16 16"><path d="M3 2l3 1 1 3-2 1a8 8 0 0 0 4 4l1-2 3 1 1 3-2 1C7 15 1 9 2 4z"/></svg>+001 555 210 4832</li>
        <li><svg viewBox="0 0 16 16"><rect x="2" y="6" width="12" height="8"/><rect x="4" y="2" width="8" height="4"/><path d="M5 9h2M9 9h2M5 11h2M9 11h2"/></svg>+001 555 210 4833</li>
        <li><svg viewBox="0 0 16 16"><circle cx="8" cy="8" r="6"/><path d="M2 8h12M8 2c-3 3-3 9 0 12M8 2c3 3 3 9 0 12"/></svg>www.quarrowsignal.com</li>
        <li><svg viewBox="0 0 16 16"><rect x="2" y="4" width="12" height="9"/><path d="M2 4l6 5 6-5"/></svg>info@quarrowsignal.com</li>
      </ul>
    </div>
  </section>

</main>
</body>
</html>
```